Northbrook Disc League - General Ultimate Flyer

This flyer is an all-purpose flyer to be used for general promotional activities run by Northbrook Disc League.

Northbrook Disc League is the recognised State body that manages the sport of Ultimate (aka: Frisbee) in Queensland. We run Ultimate events and competitions in Brisbane and around the state. We also provide coaching to schools (Primary and Secondary and we offer Level 1 Coaching certification to teachers and coaches. We have approximately 1000 members in Queensland and we are growing rapidly.

These promotional flyers are intended to excite interest about the sport from those who receive them - who are mostly people who have no prior experience or knowledge of the sport. The flyer is most importantly a pointer to the Northbrook Disc League web page www.northbrookdisc.com.au where they can access more information and make contact.

The themes we want to see expressed in the flyer are:
• Legitimate Sport,
• Athelticm and
• Fun.

The files attached contain:
• Northbrook Disc League logo
• a template flyer (the one we currently work with) and containing the suggested text. The text information is mostly right but can be edited if needed.
• a bunch of source photographs.
• Ultimate field layout diagram (use this or other if preferred).

Target Market(s)

School PE and sports teachers, school students, University students, other people looking for a new sport to play, media, potential sponsors and corporate partners. These are people who are currently NOT affiliated or familiar with the sport or our organisation.

Industry/Entity Type

Sporting Good

Requirements
Must have
• Project must create a feeling of exciting sporting legitimacy.

```html
<!DOCTYPE html>
<html lang="en">
<head>
<meta charset="utf-8">
<title>Northbrook Disc League – Play Ultimate Frisbee</title>
<link href="https://fonts.googleapis.com/css2?family=Oswald:wght@400;600;700&family=Roboto+Condensed:wght@400;700&family=Kalam:wght@700&display=swap" rel="stylesheet">
<style>
  :root{
    --red:#c8202a;
    --deep-red:#a3161e;
    --grey:#8a8a8a;
    --band-grey:#9b9b9b;
    --paper:#ffffff;
    --paper-shade:#eeeeee;
    --ink:#ffffff;
  }
  html,body{margin:0;padding:0;overflow:hidden;}
  body{width:1200px;height:2545px;}
  .flyer{
    position:relative;width:1200px;height:2545px;overflow:hidden;
    background:radial-gradient(ellipse at 70% 30%, var(--paper) 0%, var(--paper) 40%, var(--paper-shade) 100%);
    font-family:"Roboto Condensed",Arial,sans-serif;
  }
  .kicker{
    position:absolute;left:43px;top:40px;margin:0;
    font-family:"Oswald",sans-serif;font-weight:400;font-size:60px;color:var(--red);letter-spacing:1px;
  }
  .kicker strong{font-weight:700;color:var(--deep-red);}
  .headline{
    position:absolute;left:38px;top:150px;margin:0;
    font-family:"Oswald",sans-serif;font-weight:700;font-size:150px;line-height:1;color:var(--red);
  }
  .sport-band{
    position:absolute;left:0;top:338px;width:750px;height:96px;
    background:linear-gradient(#a8a8a8,var(--band-grey));
    display:flex;align-items:center;justify-content:center;
    font-family:"Oswald",sans-serif;font-weight:600;font-size:72px;color:var(--ink);letter-spacing:1px;
  }
  .org-mark{
    position:absolute;left:800px;top:220px;width:360px;
    display:flex;flex-direction:column;align-items:center;gap:20px;
  }
  .org-mark .dot{width:150px;height:150px;border-radius:50%;background:var(--red);}
  .org-mark .name{
    font-family:"Oswald",sans-serif;font-weight:700;font-size:44px;line-height:1.05;color:var(--red);text-align:center;
  }
  .hero{position:absolute;left:0;top:420px;width:1200px;height:900px;}
  .tagline{
    position:absolute;left:540px;top:1365px;width:620px;height:150px;
    transform:rotate(-8deg);transform-origin:center;
    background:var(--red);
    display:flex;align-items:center;justify-content:center;
    font-family:"Kalam",cursive;font-weight:700;font-size:92px;color:var(--ink);
    box-shadow:0 6px 10px rgba(0,0,0,.2);
  }
  .facts{
    position:absolute;left:43px;top:1615px;width:1110px;height:735px;box-sizing:border-box;
    background:linear-gradient(var(--red),var(--deep-red));
    border-radius:40px;padding:70px 60px 0 70px;
  }
  .facts ul{list-style:none;margin:0;padding:0;}
  .facts li{
    position:relative;padding-left:60px;margin-bottom:52px;
    font-size:42px;line-height:1.25;color:var(--ink);
  }
  .facts li::before{
    content:"";position:absolute;left:0;top:14px;width:26px;height:26px;border-radius:50%;
    background:#e86a6f;box-shadow:inset 0 0 0 6px #f4b5b8;
  }
  .facts b{font-weight:700;}
  .web{
    position:absolute;left:0;top:2430px;width:1200px;text-align:center;
    font-family:"Roboto Condensed",sans-serif;font-weight:700;font-size:34px;letter-spacing:6px;color:var(--red);
  }
  .foot-band{position:absolute;left:0;bottom:0;width:1200px;height:28px;background:var(--grey);}
</style>
</head>
<body>
<main class="flyer">
  <p class="kicker">Looking for a <strong>NEW SPORT??</strong></p>
  <h1 class="headline">Play…</h1>
  <div class="sport-band">ULTIMATE FRISBEE!</div>

  <div class="org-mark">
    <span class="dot"></span>
    <span class="name">Northbrook Disc League</span>
  </div>

  <svg class="hero" viewBox="0 420 1200 900" width="1200" height="900">
    <path d="M0 1250 L220 1235 Q260 1270 230 1330 L0 1345 Z" fill="var(--red)"/>
    <circle cx="60" cy="1290" r="22" fill="#ffffff"/>
    <circle cx="505" cy="830" r="380" fill="var(--red)"/>
    <circle cx="505" cy="830" r="335" fill="#ffffff"/>
    <defs>
      <linearGradient id="photoTone" x1="0" y1="0" x2="0" y2="1">
        <stop offset="0" stop-color="#6d8f5a"/>
        <stop offset="0.55" stop-color="#3f6a3c"/>
        <stop offset="1" stop-color="#5b7f3a"/>
      </linearGradient>
    </defs>
    <circle cx="505" cy="830" r="310" fill="url(#photoTone)" role="img" aria-label="Photo of two players leaping for a disc during an ultimate match on a grass field"/>
  </svg>

  <div class="tagline">Ultimate is:</div>

  <section class="facts">
    <ul>
      <li><b>A hard RUNNING, high JUMPING, full length layout DIVING, point scoring, TEAM SPORT.</b></li>
      <li><b>Non Contact</b> And Is Often Played <b>Mixed.</b></li>
      <li>One Of The Fastest Growing Sports In <b>Australia</b> And Around The <b>World.</b></li>
      <li>The Best Way To Make New <b>Friends</b> And Get <b>Fit</b> At The Same Time.</li>
    </ul>
  </section>

  <div class="web">www.northbrookdisc.com.au</div>
  <div class="foot-band"></div>
</main>
</body>
</html>
```